Mens Jewellery Homepage - Modern, Stylish Mens Ring Brand - Homepage

Project Overview: KestrelHoops.com is a men's accessories brand specializing in high-quality mens rings.

The objective of this redesign is to create a modern, visually appealing homepage that is easy to navigate, showcases a wide range of rings, highlights personalization options, and builds trust with customers.

The new design should make a strong impression while reflecting the brand's premium quality and commitment to craftsmanship.

The focus will be on a sleek aesthetic that aligns with the tastes of men shopping for wedding bands, engagement rings, or fashion accessories.

Objectives:

Modern and Sleek Aesthetic:

A clean, minimalist design that emphasizes high-quality product imagery and thoughtful use of space.
Contemporary color palette that conveys elegance and sophistication, with accents that highlight key elements without overwhelming the user.

Consistent and easy-to-read typography that reflects the brand’s modern and masculine identity.

Showcasing Products:
Hero Section: A image to show off 3 or 4 ring designs that could be used for weddings or fashion.

Product Highlights: Below the hero banner, showcase product categories by color (see current website for colors)

Featured Products: Display a selection of “Top Rated” or “Customer Favorites” rings to help guide users toward popular choices.

Personalization Section:
A dedicated section promoting the ability to personalize rings, emphasizing features like engraving with names, dates, or special messages.
Include lifestyle images of personalized rings to inspire customers and give them an idea of what’s possible.
Use callouts such as “Make It Yours” or “Personalize Your Ring” to encourage users to explore the customization options available for each product.

Building Trust:

A space to show 5 or 6 testimonials and other trust elements

Symbols / text to show

free delivery
free returns
every ring stock
fast delivery
customer images (from reviews)

Driving Conversions:
Include a prominent call-to-action (CTA) button in the hero section with text like “Shop Now” or “Discover Our Collections.”

User Experience:
Fast, easy-to-navigate layout with simple and intuitive categories. Product categories and main sections should be clearly visible and easy to access without overwhelming the user.
Design the homepage to feel cohesive and uncluttered, with a logical flow from product discovery to personalization and checkout.

Visual Elements and Imagery:
Use ring images from our site, but add backgrounds etc to make the image on the homepage more interesting.

Personalization Options: Use visual representations (like ring mockups) showing where personalization options (such as engravings) would appear on the product.

I like (and would like to see some different designs from our current design)
Vorm.com for design
ridgeloops.com

Target Market(s)

Men - 20 to 35

Number of Pages Required

1 page

Requirements
Must have
• Easy navigation, Trust, Modern, Clean,
Nice to have
• Would like to see Different designs like Vorm.com - RidgeLoops.com

```html
<!DOCTYPE html>
<html lang="en">
<head>
<meta charset="utf-8">
<title>Kestrel Hoops – Men's Rings</title>
<link href="https://fonts.googleapis.com/css2?family=Poppins:wght@600;700;800&family=Lato:wght@400;700&display=swap" rel="stylesheet">
<style>
:root{
  --ink:#111;
  --black:#000;
  --white:#fff;
  --grey:#8c8c8c;
  --light:#f2f2f2;
  --muted:#777;
  --teal-a:#16e6dd;
  --teal-b:#0fb9b1;
  --teal-soft:#c9f4f3;
  --star:#f2b01e;
  --star-off:#555;
}
*{box-sizing:border-box;margin:0;padding:0}
html,body{width:1200px;height:3786px;overflow:hidden;background:var(--white)}
body{position:relative;font-family:'Lato',sans-serif;color:var(--ink)}
.btn{position:absolute;display:flex;align-items:center;justify-content:center;border-radius:30px;background:linear-gradient(90deg,var(--teal-a),var(--teal-b));color:var(--white);font-family:'Poppins',sans-serif;font-weight:600;font-size:14px;letter-spacing:.3px}
.section-title{position:absolute;left:0;width:1200px;text-align:center;font-family:'Poppins',sans-serif;font-weight:700;font-size:41px;color:var(--black);letter-spacing:-.3px}

/* header */
.site-header{position:absolute;left:0;top:0;width:1200px;height:80px;background:var(--black)}
.brand{position:absolute;display:flex;align-items:center;gap:12px;color:var(--white);font-weight:700}
.brand-dot{width:62px;height:62px;border:3px solid var(--white);border-radius:50%}
.brand-name{font-size:19px;letter-spacing:7px;line-height:1.1}
.main-nav{position:absolute;left:463px;top:30px;display:flex;gap:32px;font-family:'Poppins',sans-serif;font-weight:600;font-size:13.5px;color:var(--white)}
.main-nav .active{border-bottom:2px solid var(--white);padding-bottom:6px}
.nav-icon{position:absolute;top:24px;width:32px;height:32px;border:2px solid var(--white);border-radius:50%}

/* hero */
.hero{position:absolute;left:0;top:80px;width:1200px;height:482px;background:radial-gradient(ellipse at 40% 60%,#7b5d52 0%,#3e2d28 55%,#1d1715 100%)}
.hero-photo{position:absolute;border:6px solid var(--white);border-radius:50%}
.hero-card{position:absolute;left:640px;top:17px;width:414px;height:414px;border-radius:50%;background:var(--white);text-align:center}
.hero-card h1{margin-top:58px;font-family:'Poppins',sans-serif;font-weight:800;font-size:55px;line-height:1.05;color:var(--black)}
.hero-card p{margin-top:22px;font-weight:700;font-size:16px}
.slider-dot{position:absolute;left:1121px;width:9px;height:9px;border-radius:50%;background:var(--white)}

/* perks */
.perks{position:absolute;left:0;top:562px;width:1200px;height:118px;background:var(--light)}
.perk{position:absolute;top:18px;display:flex;align-items:center;gap:14px;font-weight:700;font-size:17px}
.perk-icon{width:82px;height:82px;border:3px solid var(--black);border-radius:50%;display:flex;align-items:center;justify-content:center}

/* highlights */
.category{position:absolute;width:264px;text-align:center}
.category-frame{width:264px;height:264px;border:5px solid var(--grey);border-radius:78px;display:flex;align-items:center;justify-content:center}
.category-frame.is-hover{border-color:var(--teal-soft)}
.ring-shot{width:120px;height:165px;border-radius:50%}
.category-label{margin-top:38px;font-weight:700;font-size:21px;letter-spacing:.4px}

/* engrave */
.engrave{position:absolute;left:0;top:1625px;width:1200px;height:538px;background:linear-gradient(180deg,#d9d6d1,#c4c1bc)}
.engrave-halo{position:absolute;left:130px;top:28px;width:480px;height:480px;border-radius:50%;background:rgba(255,255,255,.45)}
.engrave-card{position:absolute;left:153px;top:51px;width:434px;height:434px;border-radius:50%;background:var(--white);text-align:center}
.engrave-card h2{margin-top:108px;font-family:'Poppins',sans-serif;font-weight:800;font-size:38px;line-height:1.1}
.engrave-ring{position:absolute;left:690px;top:85px;width:400px;height:360px;border-radius:50%;background:radial-gradient(ellipse at 50% 45%,#9b9a98 0%,#d3cfca 50%,rgba(0,0,0,0) 71%)}

/* favourites */
.product{position:absolute;top:2338px;width:212px;text-align:center}
.product-frame{width:212px;height:236px;border:2px solid #d0d0d0;display:flex;align-items:center;justify-content:center}
.product-frame.is-hover{border-color:var(--teal-soft)}
.product-shot{width:176px;height:178px;border-radius:50%}
.product-name{margin-top:20px;font-weight:700;font-size:16.5px;letter-spacing:.4px}
.product-price{margin-top:6px;font-size:15px;color:var(--muted)}
.quick{position:absolute;width:32px;height:32px;border-radius:50%;display:flex;align-items:center;justify-content:center}
.carousel-arrow{position:absolute;top:2431px;width:46px;height:46px;border:2px solid #999;border-radius:50%;display:flex;align-items:center;justify-content:center;background:var(--white)}
.rule{position:absolute;left:0;top:2722px;width:1200px;height:2px;background:#eee}

/* reviews */
.review{position:absolute;width:299px}
.review-card{height:146px;border:1px solid #e6e6e6;background:var(--white);padding:22px 20px 0 20px;font-size:11.2px;line-height:1.75;color:var(--muted);text-align:justify;box-shadow:0 1px 3px rgba(0,0,0,.04)}
.review-author{margin-top:12px;font-weight:700;font-size:12px;color:var(--ink)}
.avatar{position:absolute;right:16px;top:98px;width:82px;height:90px;clip-path:polygon(50% 0,100% 25%,100% 75%,50% 100%,0 75%,0 25%)}
.stars{position:relative;margin-top:18px;width:57px;height:14px;background:radial-gradient(circle,var(--star) 5px,transparent 6px) 0 0/19px 14px repeat-x}
.stars::after{content:"";position:absolute;left:57px;top:0;width:38px;height:14px;background:radial-gradient(circle,var(--star-off) 5px,transparent 6px) 0 0/19px 14px repeat-x}

/* footer */
.site-footer{position:absolute;left:0;top:3468px;width:1200px;height:232px;background:var(--black);color:var(--white)}
.footer-col{position:absolute;top:46px;font-size:13.5px;line-height:22px}
.footer-col h3{font-weight:700;font-size:16px;text-decoration:underline;margin-bottom:22px}
.social{position:absolute;top:138px;display:flex;align-items:center;gap:6px;font-weight:700;font-size:13px}
.social i{width:16px;height:16px;border-radius:50%;background:var(--white);display:block}
.legal{position:absolute;left:145px;top:3743px;font-size:13px;color:#333}
.payments{position:absolute;left:726px;top:3735px;display:flex;gap:9px;font-weight:700;font-size:12.5px;color:#333}
</style>
</head>
<body>

<header class="site-header">
  <div class="brand" style="left:145px;top:8px"><span class="brand-dot"></span><span class="brand-name">KESTREL<br>HOOPS</span></div>
  <nav class="main-nav">
    <span class="active">HOME</span><span>SHOP BY MATERIAL</span><span>SHOP BY COLOR</span><span>TRY AT HOME</span>
  </nav>
  <span class="nav-icon" style="left:985px">
    <svg width="28" height="28" viewBox="0 0 28 28"><path d="M7 9h2l2 8h8l2-6H10" fill="none" stroke="#fff" stroke-width="1.6"/><circle cx="12" cy="20" r="1.3" fill="#fff"/><circle cx="18" cy="20" r="1.3" fill="#fff"/></svg>
  </span>
  <span class="nav-icon" style="left:1024px;background:#fff">
    <svg width="28" height="28" viewBox="0 0 28 28"><circle cx="13" cy="13" r="5" fill="none" stroke="#000" stroke-width="2"/><path d="M17 17l4 4" stroke="#000" stroke-width="2"/></svg>
  </span>
</header>

<section class="hero">
  <div class="hero-photo" role="img" aria-label="Couple's hands with wedding bands" style="left:96px;top:22px;width:238px;height:238px;background:linear-gradient(135deg,#e7cbbd,#b5867a)"></div>
  <div class="hero-photo" role="img" aria-label="Hands holding silver wedding rings" style="left:316px;top:139px;width:236px;height:236px;background:linear-gradient(135deg,#c9c3c2,#7d6f6e)"></div>
  <div class="hero-photo" role="img" aria-label="Two gold rings resting on a calendar" style="left:118px;top:268px;width:216px;height:216px;background:linear-gradient(135deg,#efe9df,#c8a763)"></div>
  <div class="hero-card">
    <h1>MEN'S<br>WEDDING<br>BANDS</h1>
    <p>FALL WEDDING SALE- 20% OFF</p>
  </div>
  <a class="btn" style="left:780px;top:320px;width:134px;height:46px">SHOP NOW</a>
  <span class="slider-dot" style="top:201px"></span>
  <span class="slider-dot" style="top:221px;background:#f0cf5a"></span>
  <span class="slider-dot" style="top:241px"></span>
</section>

<section class="perks">
  <div class="perk" style="left:143px"><span class="perk-icon"><svg width="38" height="30" viewBox="0 0 38 30"><path d="M2 4h20v16H2zM22 10h8l6 6v4H22z" fill="#000"/><circle cx="9" cy="23" r="4" fill="#000" stroke="#fff" stroke-width="2"/><circle cx="28" cy="23" r="4" fill="#000" stroke="#fff" stroke-width="2"/></svg></span>Free Delivery</div>
  <div class="perk" style="left:373px"><span class="perk-icon"><svg width="34" height="34" viewBox="0 0 34 34"><path d="M8 10a12 12 0 1 1-2 9" fill="none" stroke="#000" stroke-width="3.4"/><path d="M3 6v8h8" fill="none" stroke="#000" stroke-width="3.4"/><path d="M17 11v7l4 3" fill="none" stroke="#000" stroke-width="3"/></svg></span>Free Returns</div>
  <div class="perk" style="left:600px"><span class="perk-icon"><svg width="40" height="26" viewBox="0 0 40 26"><ellipse cx="20" cy="13" rx="18" ry="11" fill="#000"/><ellipse cx="20" cy="12" rx="12" ry="4" fill="#fff"/></svg></span>Every Ring Stock</div>
  <div class="perk" style="left:853px"><span class="perk-icon"><svg width="24" height="38" viewBox="0 0 24 38"><path d="M14 1L2 22h9l-3 15 14-22h-9z" fill="#000"/></svg></span>Fast Delivery</div>
</section>

<h2 class="section-title" style="top:757px">PRODUCT HIGHLIGHTS</h2>

<div class="category" style="left:149px;top:842px"><div class="category-frame"><div class="ring-shot" role="img" aria-label="Black brushed ring" style="background:radial-gradient(ellipse,#fff 30%,#1c1c1c 33%,#555 70%,#fff 72%)"></div></div><p class="category-label">BLACK RINGS</p></div>
<div class="category" style="left:469px;top:842px"><div class="category-frame is-hover"><div class="ring-shot" role="img" aria-label="Blue and silver ring" style="background:radial-gradient(ellipse,#fff 30%,#1d47a8 33%,#9a9fa6 70%,#fff 72%)"></div></div><p class="category-label">BLUE RINGS</p></div>
<div class="category" style="left:788px;top:842px"><div class="category-frame"><div class="ring-shot" role="img" aria-label="Grey ring with wood inlay" style="background:radial-gradient(ellipse,#fff 30%,#6e6a65 33%,#a5714b 60%,#fff 72%)"></div></div><p class="category-label">BROWN RINGS</p></div>
<div class="category" style="left:149px;top:1219px"><div class="category-frame"><div class="ring-shot" role="img" aria-label="Polished gold ring" style="background:radial-gradient(ellipse,#fff 30%,#c99a1e 33%,#f2d36b 70%,#fff 72%)"></div></div><p class="category-label">GOLD RINGS</p></div>
<div class="category" style="left:469px;top:1219px"><div class="category-frame"><div class="ring-shot" role="img" aria-label="Brushed silver ring" style="background:radial-gradient(ellipse,#fff 30%,#8b8f94 33%,#d2d4d6 70%,#fff 72%)"></div></div><p class="category-label">SILVER RINGS</p></div>
<div class="category" style="left:788px;top:1219px"><div class="category-frame"><div class="ring-shot" role="img" aria-label="Rose gold and grey ring" style="background:radial-gradient(ellipse,#fff 30%,#6d6a68 33%,#d89a72 70%,#fff 72%)"></div></div><p class="category-label">ROSE GOLD RINGS</p></div>

<section class="engrave" role="img" aria-label="White wood plank background">
  <div class="engrave-halo"></div>
  <div class="engrave-card"><h2>ENGRAVE THE<br>NAMES,DATES,OR<br>SPECIAL MESSAGES</h2></div>
  <div class="engrave-ring" role="img" aria-label="Engraved antler inlay tungsten ring"></div>
  <a class="btn" style="left:262px;top:316px;width:214px;height:48px;font-size:13px">PERSONALIZE YOUR RING</a>
</section>

<h2 class="section-title" style="top:2245px">CUSTOMER FAVORITES</h2>

<span class="carousel-arrow" style="left:87px"><svg width="14" height="20" viewBox="0 0 14 20"><path d="M10 3L3 10l7 7" fill="none" stroke="#333" stroke-width="2.4"/></svg></span>
<span class="carousel-arrow" style="left:1066px"><svg width="14" height="20" viewBox="0 0 14 20"><path d="M4 3l7 7-7 7" fill="none" stroke="#333" stroke-width="2.4"/></svg></span>

<div class="product" style="left:146px"><div class="product-frame"><div class="product-shot" role="img" aria-label="Brushed silver titanium band" style="background:radial-gradient(ellipse,#fff 35%,#888c90 38%,#d6d8da 70%,#fff 72%)"></div></div><p class="product-name">PRODUCT NAME</p><p class="product-price">$56.89</p></div>
<div class="product" style="left:378px"><div class="product-frame is-hover"><div class="product-shot" role="img" aria-label="Grey meteorite pattern band" style="background:radial-gradient(ellipse,#fff 35%,#3d3d3d 38%,#7a7a7a 70%,#fff 72%)"></div></div><p class="product-name">PRODUCT NAME</p><p class="product-price">$56.89</p>
  <span class="quick" style="left:90px;top:84px;background:var(--teal-b)"><svg width="14" height="13" viewBox="0 0 14 13"><path d="M7 12L1.5 6.5A3 3 0 0 1 7 2.5a3 3 0 0 1 5.5 4z" fill="#fff"/></svg></span>
  <span class="quick" style="left:90px;top:124px;background:#111"><svg width="16" height="14" viewBox="0 0 16 14"><path d="M1 1h2l2 8h8l2-6H4" fill="none" stroke="#fff" stroke-width="1.6"/><circle cx="6" cy="12" r="1.2" fill="#fff"/><circle cx="12" cy="12" r="1.2" fill="#fff"/></svg></span>
</div>
<div class="product" style="left:610px"><div class="product-frame"><div class="product-shot" role="img" aria-label="Black and silver tungsten band" style="background:radial-gradient(ellipse,#fff 35%,#161616 38%,#9a9c9f 70%,#fff 72%)"></div></div><p class="product-name">PRODUCT NAME</p><p class="product-price">$56.89</p></div>
<div class="product" style="left:843px"><div class="product-frame"><div class="product-shot" role="img" aria-label="Black band with blue stripe" style="background:radial-gradient(ellipse,#fff 35%,#1d4bb0 38%,#111 70%,#fff 72%)"></div></div><p class="product-name">PRODUCT NAME</p><p class="product-price">$56.89</p></div>

<div class="rule"></div>

<h2 class="section-title" style="top:2788px">CUSTOMER REVIEWS</h2>

<div class="review" style="left:139px;top:2907px"><div class="review-card">" Nemo enim ipsam voluptatem quia voluptas sit aspernatur aut odit aut fugit, sed quia consequuntur magni dolores eos qui ratione voluptatem sequi nesciunt"<p class="review-author">- John Doe</p></div><span class="avatar" role="img" aria-label="Customer portrait" style="background:#c79b7e"></span><div class="stars"></div></div>
<div class="review" style="left:450px;top:2882px"><div class="review-card">" Nemo enim ipsam voluptatem quia voluptas sit aspernatur aut odit aut fugit, sed quia consequuntur magni dolores eos qui ratione voluptatem sequi nesciunt"<p class="review-author">- John Doe</p></div><span class="avatar" role="img" aria-label="Customer portrait" style="background:#9fb6cf"></span><div class="stars"></div></div>
<div class="review" style="left:762px;top:2907px"><div class="review-card">" Nemo enim ipsam voluptatem quia voluptas sit aspernatur aut odit aut fugit, sed quia consequuntur magni dolores eos qui ratione voluptatem sequi nesciunt"<p class="review-author">- John Doe</p></div><span class="avatar" role="img" aria-label="Customer portrait" style="background:#6f8ea8"></span><div class="stars"></div></div>
<div class="review" style="left:139px;top:3130px"><div class="review-card">" Nemo enim ipsam voluptatem quia voluptas sit aspernatur aut odit aut fugit, sed quia consequuntur magni dolores eos qui ratione voluptatem sequi nesciunt"<p class="review-author">- John Doe</p></div><span class="avatar" role="img" aria-label="Customer portrait" style="background:#7f93ad"></span><div class="stars"></div></div>
<div class="review" style="left:450px;top:3106px"><div class="review-card">" Nemo enim ipsam voluptatem quia voluptas sit aspernatur aut odit aut fugit, sed quia consequuntur magni dolores eos qui ratione voluptatem sequi nesciunt"<p class="review-author">- John Doe</p></div><span class="avatar" role="img" aria-label="Customer portrait" style="background:#8a6448"></span><div class="stars"></div></div>
<div class="review" style="left:762px;top:3130px"><div class="review-card">" Nemo enim ipsam voluptatem quia voluptas sit aspernatur aut odit aut fugit, sed quia consequuntur magni dolores eos qui ratione voluptatem sequi nesciunt"<p class="review-author">- John Doe</p></div><span class="avatar" role="img" aria-label="Customer portrait" style="background:#b6a79b"></span><div class="stars"></div></div>

<a class="btn" style="left:521px;top:3357px;width:158px;height:46px">SHOW MORE</a>

<footer class="site-footer">
  <div class="brand" style="left:145px;top:58px"><span class="brand-dot"></span><span class="brand-name">KESTREL<br>HOOPS</span></div>
  <span class="social" style="left:224px"><i></i>Linkr</span>
  <span class="social" style="left:284px"><i></i>Pixo</span>
  <div class="footer-col" style="left:451px"><h3>CONTACT</h3>22 Alder Row, Farnwick, FW4 7QT<br>Contact 01632 960418<br>hello@kestrelhoops.com</div>
  <div class="footer-col" style="left:773px"><h3>MENUS</h3>Home<br>Shop By Material<br>Shop By Color<br>Try At Home</div>
  <div class="footer-col" style="left:945px"><h3>LINKS</h3>Contact Us<br>Terms of Service<br>Privacy Policy<br>Blog</div>
</footer>

<p class="legal">© 2024 Kestrel Hoops - All Rights Reserved &nbsp;|&nbsp; Privacy Policy &nbsp;|&nbsp; Terms of Use</p>
<div class="payments"><span>Nexa</span><span>Orbit</span><span>Pago</span><span>Tapp</span><span>Paylo</span><span>Circa</span><span>Vesta</span></div>

</body>
</html>
```